Business Card Design Project

We are a construction company in Orange County, CA. We need a two sided business card. We would like the back to be our logo with web URL. Front should included Name, title, address, phone, fax and email address.

our address is
627 West Dorrance Blvd, Suite 308
Larkfield, NV 92718

Our logo files are attached.

Construction

```html
<!DOCTYPE html>
<html lang="en">
<head>
<meta charset="utf-8">
<title>Bravon Business Card</title>
<link href="https://fonts.googleapis.com/css2?family=Open+Sans:wght@400;700;800&family=Questrial&display=swap" rel="stylesheet">
<style>
  :root {
    --brand-blue: #174a80;
    --ink-grey: #555a60;
    --card-white: #ffffff;
    --stage: #ececec;
  }
  * { box-sizing: border-box; margin: 0; padding: 0; }
  html, body { width: 1200px; height: 444px; overflow: hidden; }
  body {
    background: var(--stage);
    font-family: "Open Sans", Arial, sans-serif;
    position: relative;
  }
  .card {
    position: absolute;
    top: 77px;
    width: 514px;
    height: 294px;
    background: var(--card-white);
    box-shadow: 0 2px 6px rgba(0,0,0,0.18);
    overflow: hidden;
  }
  .card--front { left: 66px; }
  .card--back { left: 620px; }

  .wordmark {
    font-family: "Open Sans", Arial, sans-serif;
    font-weight: 800;
    color: var(--brand-blue);
    letter-spacing: -1px;
    line-height: 1;
    font-size: 52px;
  }
  .card--front .wordmark {
    position: absolute;
    left: 40px;
    top: 104px;
  }
  .card--back .wordmark {
    position: absolute;
    left: 0; right: 0;
    top: 110px;
    text-align: center;
  }
  .back-url {
    position: absolute;
    left: 0; right: 0;
    top: 181px;
    text-align: center;
    font-size: 12px;
    letter-spacing: 2.5px;
    color: var(--ink-grey);
  }

  .contact-block {
    position: absolute;
    left: 333px;
    top: 97px;
  }
  .person-name {
    font-size: 16px;
    font-weight: 700;
    color: var(--brand-blue);
    line-height: 1.2;
  }
  .person-title {
    font-size: 13px;
    color: var(--ink-grey);
    margin-top: 4px;
  }
  .contact-list {
    list-style: none;
    margin-top: 16px;
  }
  .contact-list li {
    display: flex;
    align-items: center;
    font-size: 13px;
    color: var(--ink-grey);
    height: 18px;
  }
  .contact-list svg {
    width: 10px;
    height: 10px;
    margin-right: 8px;
    fill: var(--brand-blue);
  }

  .wave {
    position: absolute;
    left: 0; top: 0;
    width: 514px; height: 294px;
  }
  .address {
    position: absolute;
    left: 52px;
    top: 270px;
    font-family: "Questrial", Arial, sans-serif;
    font-size: 13.5px;
    color: var(--card-white);
    white-space: nowrap;
  }
</style>
</head>
<body>

<section class="card card--front">
  <svg class="wave" viewBox="0 0 514 294" aria-hidden="true">
    <defs>
      <linearGradient id="swooshFade" x1="0" x2="1">
        <stop offset="0" stop-color="#d8dadc"/>
        <stop offset="1" stop-color="#7d8186"/>
      </linearGradient>
    </defs>
    <path d="M0,245 C160,228 380,232 514,266 L514,278 C380,242 160,238 0,251 Z" fill="url(#swooshFade)"/>
    <path d="M0,253 C160,240 380,246 514,284 L514,294 L0,294 Z" fill="var(--brand-blue)"/>
  </svg>

  <div class="wordmark">BRAVON</div>

  <div class="contact-block">
    <div class="person-name">YOUR NAME</div>
    <div class="person-title">Title</div>
    <ul class="contact-list">
      <li><svg viewBox="0 0 10 10"><circle cx="5" cy="5" r="4.5" fill="none" stroke="var(--brand-blue)"/><path d="M3,2.5 L4.2,2.5 L4.6,4 L4,4.5 Q4.8,5.8 5.6,6.2 L6,5.6 L7.5,6 L7.5,7.2 Q4,7.5 3,2.5 Z"/></svg>0912345876</li>
      <li><svg viewBox="0 0 10 10"><path d="M0.5,3.5 Q5,0.5 9.5,3.5 L8.5,4.8 L7,4.2 L7,3.5 Q5,2.8 3,3.5 L3,4.2 L1.5,4.8 Z"/><rect x="2" y="5.5" width="6" height="3.5" rx="0.6"/></svg>0934512768</li>
      <li><svg viewBox="0 0 10 10"><rect x="0.5" y="2" width="9" height="6.5"/><path d="M0.5,2 L5,5.8 L9.5,2" fill="none" stroke="#fff" stroke-width="0.9"/></svg>info@bravon.com</li>
      <li><svg viewBox="0 0 10 10"><circle cx="5" cy="5" r="4.5"/><path d="M0.5,5 H9.5 M5,0.5 V9.5 M5,0.5 Q2,5 5,9.5 M5,0.5 Q8,5 5,9.5" fill="none" stroke="#fff" stroke-width="0.7"/></svg>www.bravon.com</li>
    </ul>
  </div>

  <div class="address">627 West Dorrance Blvd, Suite 308 Larkfield, NV 92718</div>
</section>

<section class="card card--back">
  <div class="wordmark">BRAVON</div>
  <div class="back-url">www.bravon.com</div>
</section>

</body>
</html>
```